Tall Fern Roofing Business Card

Need a business card with the logo that was designed here

Contact Information for Business Card

Name, Title, Phone, Email, Website, Company name

```html
<!DOCTYPE html>
<html lang="en">
<head>
<meta charset="utf-8">
<title>Tall Fern Roofing Business Card</title>
<link href="https://fonts.googleapis.com/css2?family=Montserrat:wght@400;500;700&display=swap" rel="stylesheet">
<style>
  :root {
    --bg: #d5d9dc;
    --paper: #f7f7f7;
    --brand-blue: #1f3f9c;
    --ink-grey: #4a4a4a;
    --rule-blue: #5b78c9;
  }
  * { box-sizing: border-box; margin: 0; padding: 0; }
  html, body { width: 1200px; height: 829px; overflow: hidden; }
  body {
    background: var(--bg);
    font-family: "Montserrat", sans-serif;
    position: relative;
  }
  .card {
    position: absolute;
    top: 266px;
    width: 520px;
    height: 297px;
    background: var(--paper);
    border-bottom: 4px solid var(--brand-blue);
    box-shadow: 0 10px 24px rgba(0,0,0,0.12);
  }
  .card--back { left: 50px; }
  .card--front { left: 630px; }

  .brand {
    display: flex;
    align-items: center;
    gap: 10px;
    color: var(--brand-blue);
    font-weight: 700;
    white-space: nowrap;
  }
  .brand__mark {
    background: var(--brand-blue);
    flex: none;
  }
  .card--back .brand {
    position: absolute;
    left: 150px;
    top: 44px;
    font-size: 22px;
  }
  .card--back .brand__mark { width: 14px; height: 14px; }

  .card--front .brand {
    position: absolute;
    left: 0; right: 0; top: 0; bottom: 0;
    justify-content: center;
    font-size: 36px;
    letter-spacing: 0.5px;
  }
  .card--front .brand__mark { width: 22px; height: 22px; }

  .divider {
    position: absolute;
    left: 100px;
    right: 40px;
    top: 108px;
    height: 1px;
    background: var(--rule-blue);
  }
  .contact {
    position: absolute;
    left: 30px;
    top: 128px;
    color: var(--ink-grey);
    font-size: 12.5px;
    line-height: 19px;
    list-style: none;
  }
  .contact li { display: flex; align-items: center; gap: 6px; }
  .contact svg { width: 10px; height: 10px; fill: var(--brand-blue); flex: none; }
  .contact .address { padding-left: 16px; }

  .person {
    position: absolute;
    right: 40px;
    top: 200px;
    text-align: right;
  }
  .person__name {
    color: var(--brand-blue);
    font-weight: 700;
    font-size: 17px;
    letter-spacing: 1px;
  }
  .person__title {
    color: var(--ink-grey);
    font-size: 12.5px;
    letter-spacing: 0.5px;
    margin-top: 2px;
  }
  .accent-block {
    position: absolute;
    right: 0;
    top: 200px;
    width: 14px;
    height: 38px;
    background: var(--brand-blue);
  }
</style>
</head>
<body>
  <section class="card card--back">
    <div class="brand"><span class="brand__mark"></span>Tall Fern Roofing</div>
    <div class="divider"></div>
    <ul class="contact">
      <li class="address">418 W Alder Street</li>
      <li class="address">Harlow County 6042</li>
      <li>
        <svg viewBox="0 0 10 10"><path d="M2 0.5 L4 2.5 L3 3.7 Q4.3 6 6.3 7 L7.5 6 L9.5 8 L8 9.5 Q3 9 0.5 2 Z"/></svg>
        0491 552 170
      </li>
      <li>
        <svg viewBox="0 0 10 10"><path d="M0.5 2 H9.5 V8.5 H0.5 Z M0.5 2 L5 5.5 L9.5 2" fill="none" stroke="#1f3f9c" stroke-width="1.2"/></svg>
        info@tallfernroofing.com
      </li>
      <li>
        <svg viewBox="0 0 10 10"><circle cx="5" cy="5" r="4.3" fill="none" stroke="#1f3f9c" stroke-width="1.2"/><path d="M0.7 5 H9.3 M5 0.7 Q2.5 5 5 9.3 M5 0.7 Q7.5 5 5 9.3" fill="none" stroke="#1f3f9c" stroke-width="0.9"/></svg>
        www.tallfernroofing.com
      </li>
    </ul>
    <div class="person">
      <div class="person__name">MARCUS HALE</div>
      <div class="person__title">Managing Director</div>
    </div>
    <div class="accent-block"></div>
  </section>

  <section class="card card--front">
    <div class="brand"><span class="brand__mark"></span>Tall Fern Roofing</div>
  </section>
</body>
</html>
```